Quillbrookes websites redesign

Www.quill-brookes.com needs to be redesigned along with updations. The incremental material will be provided for the updations. We are looking for complete redesign of the pages with the new content. The complete write up will be provided soon

Target Market(s)

Global

Coding

Coded - Design and coding required

Number of Pages Required

5+ page

Requirements
Must have
• A clean and slick design for the Consulting.
Should not have
• Too many pictures which reduces the speed of the site

```html
<!DOCTYPE html>
<html lang="en">
<head>
<meta charset="utf-8">
<title>Quillbrookes Consultancy Limited</title>
<link rel="stylesheet" href="https://fonts.googleapis.com/css2?family=Open+Sans:wght@400;600&family=Raleway:wght@400;500;600&display=swap">
<style>
:root{
  --maroon:#6b2325;
  --maroon-deep:#5e1f20;
  --blue:#2d9bd2;
  --blue-light:#4cb3df;
  --blue-text:#2f9ad0;
  --ink:#3a3a3a;
  --grey:#6e6e6e;
  --white:#ffffff;
}
*{margin:0;padding:0;box-sizing:border-box}
html,body{width:766px;height:1200px;overflow:hidden;background:var(--white)}
body{position:relative;font-family:"Open Sans",Arial,sans-serif;color:var(--ink)}
.abs{position:absolute}

/* header */
.site-header{position:absolute;left:0;top:0;width:766px;height:66px;background:var(--white)}
.brand{position:absolute;left:96px;top:22px;display:flex;align-items:center;gap:7px;font-family:"Raleway",sans-serif;font-size:20px;font-weight:500;color:var(--maroon)}
.brand-dot{width:22px;height:22px;border-radius:50%;background:var(--blue)}
.main-nav{position:absolute;top:30px;left:271px;display:flex;gap:0;font-family:"Raleway",sans-serif;font-size:10px;font-weight:500;letter-spacing:.2px}
.main-nav a{color:#444;text-decoration:none;margin-right:21px;position:relative}
.main-nav a.active{color:var(--blue-text)}
.main-nav a.active::after{content:"";position:absolute;left:-4px;right:-4px;top:32px;height:2px;background:var(--blue-text)}

/* hero */
.hero{position:absolute;left:0;top:66px;width:766px;height:317px;background:linear-gradient(100deg,#8a9aaa 0%,#c9d6e2 35%,#a9c3da 60%,#dfe9f1 100%)}
.hero-caption{position:absolute;left:79px;top:129px;width:304px;height:89px;background:rgba(107,35,37,.82);padding:20px 0 0 20px;color:var(--white);font-family:"Raleway",sans-serif;font-weight:500}
.hero-caption .small{font-size:16.5px;letter-spacing:.3px;line-height:19px}
.hero-caption .large{font-size:22.5px;letter-spacing:.3px;line-height:28px}
.hero-dots{position:absolute;left:359px;top:290px;display:flex;gap:3px}
.hero-dots span{width:11px;height:11px;border-radius:50%;background:var(--white)}
.hero-dots span.on{background:#f07a1a;border:2px solid var(--white)}

/* intro */
.intro-map{position:absolute;left:190px;top:400px;width:390px;height:198px;background:radial-gradient(ellipse at center,#ededed 0%,rgba(240,240,240,.5) 55%,rgba(255,255,255,0) 75%)}
.intro-title{position:absolute;left:0;top:415px;width:766px;text-align:center;font-family:"Raleway",sans-serif;font-size:24px;font-weight:500;color:var(--maroon)}
.intro-sub{position:absolute;left:0;top:446px;width:766px;text-align:center;font-family:"Raleway",sans-serif;font-size:15px;color:var(--maroon)}
.intro-text{position:absolute;left:100px;width:566px;text-align:center;font-size:8px;line-height:12.5px;color:var(--grey)}

/* services band */
.services{position:absolute;left:0;top:598px;width:766px;height:240px;background:linear-gradient(120deg,#2a8fc6 0%,#3aa6d8 45%,#2b93cb 100%)}
.notch{position:absolute;left:0;top:598px}
.service{position:absolute;top:650px;width:220px;text-align:center;color:var(--white)}
.service svg{display:block;margin:0 auto}
.service h3{margin-top:14px;font-family:"Raleway",sans-serif;font-size:13px;font-weight:500;letter-spacing:.3px}
.service p{margin-top:7px;font-size:7.4px;line-height:11px;opacity:.92}
.btn{display:inline-block;margin-top:15px;width:69px;height:21px;border:1.5px solid var(--white);font-size:8px;line-height:18px;color:var(--white);text-decoration:none}

/* blogs */
.blogs-title{position:absolute;left:0;top:866px;width:766px;text-align:center;font-family:"Raleway",sans-serif;font-size:20px;color:var(--blue-text)}
.post{position:absolute;top:909px;width:179px}
.post-image{position:relative;width:179px;height:93px}
.post-date{position:absolute;left:0;bottom:0;width:96px;height:19px;background:rgba(47,154,208,.85);color:var(--white);font-size:9px;line-height:19px;padding-left:10px}
.post h4{margin-top:9px;padding-left:2px;font-family:"Raleway",sans-serif;font-size:11px;font-weight:500;color:var(--maroon)}
.post p{margin-top:3px;padding-left:2px;font-size:7px;line-height:10px;color:var(--grey)}
.post a{display:block;margin-top:4px;padding-left:2px;font-size:7.4px;color:var(--blue-text);text-decoration:none}

/* footer */
.site-footer{position:absolute;left:0;top:1117px;width:766px;height:83px;background:var(--maroon-deep)}
.foot-nav{position:absolute;left:93px;top:24px;display:flex;font-family:"Raleway",sans-serif;font-size:8.8px;font-weight:500;color:var(--white)}
.foot-nav span{margin-right:14px}
.copyright{position:absolute;left:93px;top:44px;font-size:7px;color:#e6d6d6}
.social{position:absolute;left:471px;top:23px;display:flex;gap:1px}
.social span{width:16px;height:16px;border:1.2px solid var(--white);border-radius:50%}
.foot-brand{position:absolute;left:563px;top:20px;display:flex;align-items:center;gap:6px;font-family:"Raleway",sans-serif;font-size:17px;font-weight:500;color:#b89595}
.foot-brand i{width:18px;height:18px;border-radius:50%;background:#b89595;display:block}
</style>
</head>
<body>

<header class="site-header">
  <div class="brand"><span class="brand-dot"></span>Quillbrookes</div>
  <nav class="main-nav">
    <a class="active">HOME</a><a>FOUNDER</a><a>CONSULTANCY</a><a>SYSTEM</a><a>CASE STUDIES</a><a>CONTACT</a>
  </nav>
</header>

<section class="hero" role="img" aria-label="Photo of three business consultants in a meeting">
  <div class="hero-caption">
    <div class="small">TRADE AND INVESTMENT</div>
    <div class="large">CONSULTANCY SERVICE</div>
  </div>
  <div class="hero-dots"><span class="on"></span><span></span><span></span><span></span></div>
</section>

<div class="intro-map" role="img" aria-label="Faint world map"></div>
<h1 class="intro-title">Quillbrookes Consultancy Limited</h1>
<h2 class="intro-sub">Mauris vel lacus vitae felis vestibulum volutpat</h2>
<p class="intro-text" style="top:478px">We capitalizes on synergies arising from trade and investment linkages between countries and knowledge of traditional and non-traditional pools of liquidity to provide consultancy services to Emerging country banks, Corporates and SMEs.</p>
<p class="intro-text" style="top:512px">The Consultancy provides bank neutral views to Corporates and SMEs in Asian emerging markets and helps in improving financial structure and efficient use of funds. Our endeavor is to provide a distinct bottom line advantage to our clients. The primary focus is in regionalisation of the banking relationship across the globe, providing structured finance solutions and off balance sheet solutions.</p>

<section class="services" role="img" aria-label="Blue toned photo of a glass office building"></section>
<svg class="notch" width="766" height="30" viewBox="0 0 766 30">
  <path d="M330 0 C352 0 358 26 383 26 C408 26 414 0 436 0 Z" fill="#ffffff"/>
  <circle cx="383" cy="12" r="9" fill="#2d9bd2"/>
</svg>

<div class="service" style="left:80px">
  <svg width="50" height="46" viewBox="0 0 50 46" fill="#fff">
    <circle cx="30" cy="18" r="15"/>
    <text x="30" y="25" font-size="19" font-family="Open Sans,sans-serif" font-weight="600" text-anchor="middle" fill="#2d9bd2">$</text>
    <path d="M2 32 h8 l12 4 h12 a3 3 0 0 1 0 6 h-12 v-1 h12 M10 44 h-8 z"/>
    <rect x="2" y="31" width="7" height="13"/>
    <path d="M10 33 q8 -3 14 1 h12 q5 0 10 -4 l2 2 q-6 8 -14 9 h-24 z"/>
  </svg>
  <h3>FINANCIAL SERVICE</h3>
  <p>Mauris vel lacus vitae felis vestibulum volutpat<br>Eeu imperdiet ac nisl Cum sociis natoque<br>penatibus et magnis dis parturi</p>
  <a class="btn">Read More</a>
</div>

<div class="service" style="left:275px">
  <svg width="50" height="46" viewBox="0 0 50 46" fill="#fff">
    <circle cx="20" cy="11" r="9"/>
    <path d="M4 46 v-10 q0 -11 16 -11 q16 0 16 11 v10 z"/>
    <path d="M29 2 h19 v11 h-12 l-4 4 v-4 h-3 z" fill="none" stroke="#fff" stroke-width="1.6"/>
  </svg>
  <h3>CONSULTANCY</h3>
  <p>Mauris vel lacus vitae felis vestibulum volutpat<br>Eeu imperdiet ac nisl Cum sociis natoque<br>penatibus et magnis dis parturi</p>
  <a class="btn">Read More</a>
</div>

<div class="service" style="left:477px">
  <svg width="50" height="46" viewBox="0 0 50 46" fill="#fff">
    <path d="M25 0 l14 7 h-28 z"/>
    <rect x="13" y="9" width="3" height="10"/><rect x="20" y="9" width="3" height="10"/><rect x="27" y="9" width="3" height="10"/><rect x="34" y="9" width="3" height="10"/>
    <rect x="11" y="19" width="28" height="3"/>
    <path d="M25 22 v5 M8 30 h34" stroke="#fff" stroke-width="1.2" stroke-dasharray="2 1.5" fill="none"/>
    <circle cx="8" cy="35" r="3"/><path d="M2 46 q0 -8 6 -8 q6 0 6 8 z"/>
    <circle cx="25" cy="35" r="3"/><path d="M19 46 q0 -8 6 -8 q6 0 6 8 z"/>
    <circle cx="42" cy="35" r="3"/><path d="M36 46 q0 -8 6 -8 q6 0 6 8 z"/>
  </svg>
  <h3>BANKING RELATIONSHIP</h3>
  <p>Mauris vel lacus vitae felis vestibulum volutpat<br>eu imperdiet ac nisl Cum sociis natoque<br>penatibus et magnis dis parturi</p>
  <a class="btn">Read More</a>
</div>

<h2 class="blogs-title">Latest Blogs</h2>

<article class="post" style="left:101px">
  <div class="post-image" role="img" aria-label="Photo of a bank building sign against glass facade" style="background:linear-gradient(160deg,#2f5f8f,#7fa8c9 60%,#c8d4df)">
    <span class="post-date">26 Dec, 2015</span>
  </div>
  <h4>Praesent elementum elit</h4>
  <p>tellus Curabitur metus ipsum luctus eu male suada ut tincidunt sed diam Donec quis mi sed magna hendrerit Suspendisse</p>
  <a>Learn More</a>
</article>

<article class="post" style="left:300px">
  <div class="post-image" role="img" aria-label="Photo of a business team presentation in an office" style="background:linear-gradient(160deg,#e3e8ec,#b9c3cc 55%,#8b97a4)">
    <span class="post-date">29 Dec, 2015</span>
  </div>
  <h4>Nulla rhoncus dictum metus</h4>
  <p>tellus Curabitur metus ipsum luctus eu male suada ut tincidunt sed diam Donec quis mi sed magna hendrerit Suspendisse</p>
  <a>Learn More</a>
</article>

<article class="post" style="left:498px">
  <div class="post-image" role="img" aria-label="Photo of colleagues reviewing documents together" style="background:linear-gradient(160deg,#d9c8b8,#b49a86 50%,#e7e3de)">
    <span class="post-date">30 Dec, 2015</span>
  </div>
  <h4>Suspendisse risus nibh</h4>
  <p>tellus Curabitur metus ipsum luctus eu male suada ut tincidunt sed diam Donec quis mi sed magna hendrerit Suspendisse</p>
  <a>Learn More</a>
</article>

<footer class="site-footer">
  <div class="foot-nav"><span>HOME</span><span>FOUNDER</span><span>CONSULTANCY</span><span>SYSTEM</span><span>CASE STUDIES</span><span>CONTACT</span></div>
  <div class="copyright">© 2016 Company Name&nbsp; All right reserved&nbsp; Term of Use</div>
  <div class="social"><span></span><span></span><span></span><span></span></div>
  <div class="foot-brand"><i></i>Quillbrookes</div>
</footer>

</body>
</html>
```